Veldmark Supplies Business Card

Professional business card that stand out to our potential customers. Front and back with clean modern design

Industry/Entity Type

Oil and gas

Contact Information for Business Card

Name, address, website , office phone and cell number

Requirements
Must have
• Editable files for each employee

```html
<!DOCTYPE html>
<html lang="en">
<head>
<meta charset="utf-8">
<title>Veldmark Supplies – Business Card</title>
<link rel="stylesheet" href="https://fonts.googleapis.com/css2?family=Montserrat:wght@400;700&display=swap">
<style>
  :root {
    --stage: #2e2e30;
    --card-dark: #231f20;
    --brand-red: #ed1f24;
    --brand-cyan: #10b0d2;
    --paper: #ffffff;
  }
  * { margin: 0; padding: 0; box-sizing: border-box; }
  html, body { width: 1200px; height: 1059px; overflow: hidden; }
  body {
    background: var(--stage);
    font-family: "Montserrat", Arial, sans-serif;
    position: relative;
  }
  .card {
    position: absolute;
    width: 690px;
    height: 392px;
    border-radius: 18px;
    overflow: hidden;
    background: var(--card-dark);
  }
  .card-front { left: 255px; top: 100px; }
  .card-back { left: 255px; top: 537px; }

  .front-shapes { position: absolute; inset: 0; width: 100%; height: 100%; }

  .holder { position: absolute; left: 25px; top: 82px; }
  .holder-name {
    font-weight: 700; font-size: 29px; line-height: 1;
    color: var(--brand-cyan); letter-spacing: 0.3px;
  }
  .holder-role {
    margin-top: 5px; font-size: 15px; color: var(--paper);
  }

  .contact-list {
    position: absolute; left: 25px; top: 233px; list-style: none;
  }
  .contact-list li {
    display: flex; align-items: center; gap: 8px;
    height: 23.5px; font-size: 16.5px; color: var(--paper);
  }
  .contact-list svg { width: 13px; height: 13px; flex: none; }
  .divider {
    position: absolute; left: 25px; top: 333px;
    width: 13px; height: 1.5px; background: var(--brand-red);
  }
  .address {
    position: absolute; left: 25px; top: 346px;
    display: flex; align-items: center; gap: 8px;
    font-size: 16.5px; color: var(--paper);
  }
  .address svg { width: 12px; height: 17px; flex: none; }

  .brand {
    position: absolute; display: flex; align-items: center;
  }
  .brand-front { left: 395px; top: 240px; width: 290px; justify-content: center; gap: 9px; }
  .brand-front .brand-mark { width: 16px; height: 16px; background: var(--brand-cyan); }
  .brand-front .brand-name { font-weight: 700; font-size: 21px; color: var(--brand-red); letter-spacing: 0.5px; }

  .brand-back { inset: 0; justify-content: center; gap: 16px; }
  .brand-back .brand-mark { width: 30px; height: 30px; background: var(--brand-cyan); }
  .brand-back .brand-name { font-weight: 700; font-size: 40px; color: var(--brand-red); letter-spacing: 0.5px; }
</style>
</head>
<body>

<section class="card card-front">
  <svg class="front-shapes" viewBox="0 0 690 392" preserveAspectRatio="none" aria-hidden="true">
    <polygon points="262,0 690,0 690,392 478,392" fill="var(--paper)"/>
    <polygon points="234,0 262,0 478,392 470,392" fill="var(--brand-red)"/>
    <polygon points="0,78 290,78 326,144 0,144" fill="var(--brand-red)"/>
  </svg>

  <div class="holder">
    <h1 class="holder-name">Daniel Corwin</h1>
    <p class="holder-role">Manager</p>
  </div>

  <ul class="contact-list">
    <li>
      <svg viewBox="0 0 16 16"><path d="M3 1.5l3 3-1.6 1.8a9 9 0 0 0 5.3 5.3L11.5 10l3 3-2 2C6.5 15 1 9.5 1 3.5z" fill="var(--brand-red)"/></svg>
      1-604-555-0148
    </li>
    <li>
      <svg viewBox="0 0 16 16"><rect x="1" y="3" width="14" height="10" rx="1" fill="var(--brand-cyan)"/><path d="M1.5 4l6.5 5 6.5-5" stroke="var(--card-dark)" stroke-width="1.2" fill="none"/></svg>
      dcorwin@veldparts.vn
    </li>
    <li>
      <svg viewBox="0 0 16 16" fill="none" stroke="var(--brand-red)" stroke-width="1.2"><circle cx="8" cy="8" r="6.5"/><ellipse cx="8" cy="8" rx="3" ry="6.5"/><path d="M1.5 8h13M2.5 5h11M2.5 11h11"/></svg>
      www.veldparts.vn
    </li>
    <li>
      <svg viewBox="0 0 16 16" fill="none" stroke="var(--brand-cyan)" stroke-width="1.2"><circle cx="8" cy="8" r="6.5"/><ellipse cx="8" cy="8" rx="3" ry="6.5"/><path d="M1.5 8h13M2.5 5h11M2.5 11h11"/></svg>
      www.veldparts.com
    </li>
  </ul>
  <div class="divider"></div>
  <p class="address">
    <svg viewBox="0 0 12 17"><path d="M6 0a6 6 0 0 0-6 6c0 4.5 6 11 6 11s6-6.5 6-11a6 6 0 0 0-6-6zm0 8.5A2.5 2.5 0 1 1 6 3.5a2.5 2.5 0 0 1 0 5z" fill="var(--brand-cyan)"/></svg>
    Ho Chi Minh, Vietnam
  </p>

  <div class="brand brand-front">
    <span class="brand-mark"></span>
    <span class="brand-name">Veldmark Supplies</span>
  </div>
</section>

<section class="card card-back">
  <div class="brand brand-back">
    <span class="brand-mark"></span>
    <span class="brand-name">Veldmark Supplies</span>
  </div>
</section>

</body>
</html>
```